TALMORK

The business want a professional looking business card. We have a scetch we will add but want the extra upgrade, and would like more suggestions for variations of our business cards.

```html
<!DOCTYPE html>
<html lang="en">
<head>
<meta charset="utf-8">
<title>TALMORK Business Cards</title>
<link rel="stylesheet" href="https://fonts.googleapis.com/css2?family=Playfair+Display:wght@700;900&family=Lato:wght@400;700&display=swap">
<style>
  :root {
    --page-bg: #8f8f8f;
    --card-bg: #1d1d1d;
    --gold-deep: #a87a2c;
    --gold-mid: #d2a43c;
    --gold-light: #f3e585;
    --gold-text: #c99a3c;
    --text-light: #f2f2f2;
  }
  * { box-sizing: border-box; margin: 0; padding: 0; }
  html, body {
    width: 1200px;
    height: 1200px;
    overflow: hidden;
    background: var(--page-bg);
  }
  .sheet {
    position: relative;
    width: 1200px;
    height: 1200px;
  }
  .card {
    position: absolute;
    left: 281px;
    width: 642px;
    height: 366px;
    background: var(--card-bg);
    border-radius: 20px;
    overflow: hidden;
  }
  .card--front { top: 195px; }
  .card--back { top: 639px; }

  .ornament {
    position: absolute;
    top: 6px;
    width: 184px;
    height: 354px;
    background: linear-gradient(160deg, var(--gold-deep) 0%, var(--gold-mid) 35%, var(--gold-light) 70%, var(--gold-mid) 100%);
  }
  .card--front .ornament { right: 0; border-radius: 184px 0 0 184px; }
  .card--back .ornament { left: 0; border-radius: 0 184px 184px 0; }

  .holder {
    position: absolute;
    left: 77px;
    top: 104px;
  }
  .holder__name {
    font-family: "Playfair Display", serif;
    font-weight: 900;
    font-size: 27px;
    line-height: 1.1;
    color: var(--gold-text);
  }
  .holder__role {
    font-family: "Lato", sans-serif;
    font-size: 16px;
    color: var(--text-light);
    margin-top: 2px;
  }
  .holder__rule {
    width: 72px;
    height: 2px;
    margin-top: 18px;
    background: linear-gradient(90deg, var(--gold-deep), var(--gold-light), var(--gold-deep));
  }
  .contact {
    list-style: none;
    margin-top: 22px;
  }
  .contact__item {
    display: flex;
    align-items: center;
    gap: 11px;
    font-family: "Lato", sans-serif;
    font-size: 14px;
    letter-spacing: 0.3px;
    color: var(--text-light);
    height: 22px;
  }
  .contact__icon { width: 13px; height: 13px; flex: none; }

  .brand {
    position: absolute;
    left: 184px;
    right: 0;
    top: 0;
    bottom: 0;
    display: flex;
    align-items: center;
    justify-content: center;
  }
  .brand__name {
    font-family: "Playfair Display", serif;
    font-weight: 700;
    font-size: 42px;
    letter-spacing: 10px;
    color: var(--gold-text);
    margin-right: -10px;
  }
</style>
</head>
<body>
<main class="sheet">
  <section class="card card--front">
    <div class="holder">
      <h1 class="holder__name">Arne Lukas Brekkestad</h1>
      <p class="holder__role">CEO &amp; Founder</p>
      <div class="holder__rule"></div>
      <ul class="contact">
        <li class="contact__item">
          <svg class="contact__icon" viewBox="0 0 16 16" aria-hidden="true"><path fill="#c99a3c" d="M3.2 1.5l2.3 2.6-1.2 1.7c.9 2 2.4 3.6 4.4 4.6l1.7-1.3 2.6 2.3-1.3 2.3C6.7 13.7 2.2 9.2 1 4.2z"/></svg>
          <span>004791846203</span>
        </li>
        <li class="contact__item">
          <svg class="contact__icon" viewBox="0 0 16 16" aria-hidden="true"><rect x="1" y="3" width="14" height="10" fill="#c99a3c"/><path d="M1.5 3.5L8 9l6.5-5.5" fill="none" stroke="#1d1d1d" stroke-width="1.3"/></svg>
          <span>talmork.llc@mailhub.com</span>
        </li>
        <li class="contact__item">
          <svg class="contact__icon" viewBox="0 0 16 16" aria-hidden="true"><circle cx="8" cy="8" r="6.5" fill="none" stroke="#c99a3c" stroke-width="1.6"/><ellipse cx="8" cy="8" rx="2.6" ry="6.5" fill="none" stroke="#c99a3c" stroke-width="1.2"/><path d="M1.5 8h13" stroke="#c99a3c" stroke-width="1.2"/></svg>
          <span>www.talmork.llc</span>
        </li>
      </ul>
    </div>
    <div class="ornament" role="img" aria-label="Gold leaf-and-dot ornament bleeding off the right edge"></div>
  </section>

  <section class="card card--back">
    <div class="ornament" role="img" aria-label="Gold leaf-and-dot ornament bleeding off the left edge"></div>
    <div class="brand">
      <span class="brand__name">TALMORK</span>
    </div>
  </section>
</main>
</body>
</html>
```